Post it Note design

POST-IT NOTE DESIGN (CONTENT)
Size recommended: 4x6 for handwriting space.
Header (Bold):
Lighting Issue Detected on Your Property
Sub-header:
During our routine night inspection, we noted the following item(s):
Checkbox List:
⬜ Building Lights Out
⬜ Pole Lights Out
⬜ Sign Not Illuminated
⬜ Other ________________________
Action Line:
We can provide a quote or dispatch service right away.
Area for notes
Contact Block (Bold & Centered):
Lumivale Fixture Inc.
Service@LumivaleFixture.com
www.LumivaleFixture.com
877-555-0148
Industry/Entity Type
Electrical lighting
Colors
Designer to choose colors to be used in the design.
Look and feel
Each slider illustrates characteristics of the customer's brand and the style your logo design should communicate.

```html
<!DOCTYPE html>
<html lang="en">
<head>
<meta charset="utf-8">
<title>Lumivale Fixture Inc. – Lighting Issue Note</title>
<link href="https://fonts.googleapis.com/css2?family=Montserrat:wght@400;500;600;700;800&display=swap" rel="stylesheet">
<style>
  :root {
    --bg: #a9a9a9;
    --paper: #ffffff;
    --brand-red: #e31e2c;
    --band-red-top: #e8213a;
    --band-red-bottom: #9c0f28;
    --navy: #2b3990;
    --band-navy-left: #1d3f8a;
    --band-navy-right: #0c1540;
    --ink: #111111;
    --strip-tint: #b8c2da;
    --van-tone: #e7e9ee;
  }
  * { margin: 0; padding: 0; box-sizing: border-box; }
  html, body { width: 1200px; height: 1200px; overflow: hidden; }
  body {
    background: var(--bg);
    font-family: "Montserrat", sans-serif;
    position: relative;
  }
  .note {
    position: absolute;
    left: 220px; top: 30px;
    width: 759px; height: 1140px;
    background: var(--paper);
    overflow: hidden;
  }
  .brand-name {
    position: absolute;
    left: 0; right: 0; top: 62px;
    text-align: center;
    color: var(--brand-red);
    font-weight: 800;
    font-size: 70px;
    line-height: 1.15;
    text-transform: uppercase;
    letter-spacing: 1px;
  }
  .band { position: absolute; left: 0; width: 759px; }
  .band svg { position: absolute; inset: 0; width: 100%; height: 100%; }
  .band-text {
    position: absolute; left: 0; right: 0;
    text-align: center; color: #fff;
    text-shadow: 0 2px 3px rgba(0,0,0,.45);
    text-transform: uppercase;
  }
  .alert-band { top: 301px; height: 141px; }
  .alert-band .band-text {
    top: 28px; padding-left: 40px;
    font-weight: 800; font-size: 39px; line-height: 44px; letter-spacing: 1px;
  }
  .intro {
    position: absolute; left: 0; right: 0; top: 458px;
    text-align: center; color: var(--navy);
    font-size: 27px; line-height: 34px; font-weight: 400;
    padding-left: 10px;
  }
  .intro strong { font-weight: 700; }
  .check-item {
    position: absolute;
    display: flex; align-items: center;
    color: var(--navy); font-weight: 700; font-size: 25px;
  }
  .check-box {
    width: 24px; height: 24px;
    border: 2px solid #333; margin-right: 14px; flex: none;
  }
  .other-line {
    display: inline-block; width: 186px; height: 2px;
    background: var(--navy); margin-left: 2px; align-self: flex-end; margin-bottom: 3px;
  }
  .list-divider {
    position: absolute; left: 363px; top: 556px;
    width: 2px; height: 85px; background: #333;
  }
  .action-band { top: 679px; height: 104px; }
  .action-band .band-text {
    top: 23px;
    font-weight: 800; font-size: 27px; line-height: 33px; letter-spacing: -0.5px;
  }
  .notes {
    position: absolute; left: 44px; width: 660px;
    font-size: 22px; font-weight: 500; color: var(--ink);
  }
  .notes-row { height: 44px; display: flex; align-items: flex-end; }
  .notes-row .dots {
    flex: 1; border-bottom: 3px dotted #222; margin-bottom: 6px; margin-left: 2px;
  }
  .contact-strip {
    position: absolute; left: 0; top: 952px; width: 759px; height: 61px;
    background: linear-gradient(90deg, var(--strip-tint) 0%, #dfe4ef 70%, #ffffff 100%);
  }
  .contact-name {
    position: absolute; left: 0; right: 0; top: 0;
    text-align: center; line-height: 61px;
    color: var(--navy); font-weight: 800; font-size: 46px;
    word-spacing: 10px; padding-left: 20px;
  }
  .contact-web {
    position: absolute; left: 0; right: 0; top: 1019px;
    text-align: center; font-weight: 700; font-size: 19px; color: var(--ink);
  }
  .contact-web .accent { color: var(--navy); }
  .phone {
    position: absolute; left: 162px; top: 1046px;
    display: flex; align-items: center;
  }
  .phone svg { width: 36px; height: 40px; margin-right: 6px; }
  .phone-number {
    color: var(--brand-red); font-weight: 800; font-size: 56px; letter-spacing: -1px;
  }
  .vehicle {
    position: absolute;
    background: linear-gradient(180deg, #f4f5f8 0%, var(--van-tone) 70%, #c9ccd4 100%);
    border-radius: 10px;
  }
  .vehicle.van { left: 27px; top: 1045px; width: 131px; height: 78px; }
  .vehicle.truck { left: 603px; top: 1038px; width: 153px; height: 89px; }
  .bottom-strip { position: absolute; left: 0; top: 1127px; height: 13px; }
  .bottom-strip.red { width: 381px; background: var(--brand-red); }
  .bottom-strip.navy { left: 383px; width: 376px; background: var(--navy); }
</style>
</head>
<body>
  <main class="note">
    <div class="brand-name">Lumivale<br>Fixture Inc.</div>

    <section class="band alert-band">
      <svg viewBox="0 0 759 141" preserveAspectRatio="none" aria-hidden="true">
        <defs>
          <linearGradient id="redBand" x1="0" y1="0" x2="0" y2="1">
            <stop offset="0" stop-color="var(--band-red-top)"/>
            <stop offset="1" stop-color="var(--band-red-bottom)"/>
          </linearGradient>
        </defs>
        <path d="M10 141 L50 20 Q58 0 85 0 L759 0 L759 141 Z" fill="url(#redBand)"/>
      </svg>
      <h1 class="band-text">Lighting Issue Detected<br>On Your Property</h1>
    </section>

    <p class="intro">During our <strong>routine night inspection,</strong><br>we noted the following item(s):</p>

    <div class="check-item" style="left:51px; top:554px;"><span class="check-box"></span>Building Lights Out</div>
    <div class="check-item" style="left:51px; top:615px;"><span class="check-box"></span>Pole Lights Out</div>
    <div class="list-divider"></div>
    <div class="check-item" style="left:399px; top:554px;"><span class="check-box"></span>Sign Not Illuminated</div>
    <div class="check-item" style="left:399px; top:615px;"><span class="check-box"></span>Other<span class="other-line"></span></div>

    <section class="band action-band">
      <svg viewBox="0 0 759 104" preserveAspectRatio="none" aria-hidden="true">
        <defs>
          <linearGradient id="navyBand" x1="0" y1="0" x2="1" y2="0">
            <stop offset="0" stop-color="var(--band-navy-left)"/>
            <stop offset="0.55" stop-color="#111d52"/>
            <stop offset="1" stop-color="var(--band-navy-right)"/>
          </linearGradient>
        </defs>
        <path d="M23 104 L50 18 Q57 0 80 0 L759 0 L759 104 Z" fill="url(#navyBand)"/>
      </svg>
      <h2 class="band-text">We can provide a quote or dispatch<br>service right away</h2>
    </section>

    <div class="notes" style="top:796px;">
      <div class="notes-row">NOTES<span class="dots"></span></div>
      <div class="notes-row"><span class="dots"></span></div>
      <div class="notes-row"><span class="dots"></span></div>
    </div>

    <div class="contact-strip"><div class="contact-name">Lumivale Fixture Inc.</div></div>
    <p class="contact-web">Service@LumivaleFixture.com | www.<span class="accent">LumivaleFixture</span>.com</p>

    <div class="vehicle van" role="img" aria-label="Photo of the company's white service van"></div>

    <div class="phone">
      <svg viewBox="0 0 36 40" aria-hidden="true">
        <path d="M8 4 L14 4 L16 13 L12 16 Q14 24 20 29 L24 25 L32 28 L32 34 Q30 38 25 37 Q6 32 3 11 Q3 6 8 4 Z" fill="var(--navy)"/>
        <path d="M22 6 Q30 10 32 18" stroke="var(--navy)" stroke-width="2.5" fill="none" stroke-linecap="round"/>
        <path d="M21 11 Q26 13 27 18" stroke="var(--navy)" stroke-width="2.5" fill="none" stroke-linecap="round"/>
      </svg>
      <span class="phone-number">877-555-0148</span>
    </div>

    <div class="vehicle truck" role="img" aria-label="Photo of the company's white bucket truck with safety cones"></div>

    <div class="bottom-strip red"></div>
    <div class="bottom-strip navy"></div>
  </main>
</body>
</html>
```